Simple proffessional BC

I have a logo which I will attach below.
I would like the logo on the front of the card with these details in point form below:
Pre and Post Natal Yoga: Pregnancy Workshops: Hypnobirthing Courses
On the back of the card my details:
Marla Pennick
Facebook page- stretchbelliesbayridgefield
Mobile- 0491 352 718

I like the idea of the card being simple, possibly just the above on a plain coloured (eggshell?) card, a card that is textured.
I am open to suggestion if it appeals!
Thank you and good luck!

Target Market(s)

Pregnant women, 20's-40's

Requirements
Must have
• Simple, compliment logo.
Make logo the feature.
Should not have

• .

```html
<!DOCTYPE html>
<html lang="en">
<head>
<meta charset="utf-8">
<title>Stretch Bellies – Business Card</title>
<link rel="stylesheet" href="https://fonts.googleapis.com/css2?family=Montserrat:wght@400;500;600&display=swap">
<style>
  :root {
    --page: #e9e6e1;
    --card: #fbfaf8;
    --card-shade: #eeece8;
    --wine: #8c2a2f;
    --gold: #f0a92e;
    --gold-light: #f6c867;
    --ink: #4a4446;
    --accent: #f2a33a;
  }
  * { box-sizing: border-box; margin: 0; padding: 0; }
  html, body {
    width: 1200px; height: 899px; overflow: hidden;
    background: var(--page);
    font-family: "Montserrat", Arial, sans-serif;
  }
  .canvas {
    position: relative; width: 1200px; height: 899px;
    display: flex; align-items: center; justify-content: center; gap: 50px;
  }
  .card {
    position: relative; width: 520px; height: 300px;
    border-radius: 30px; overflow: hidden;
    background: radial-gradient(circle at 60% 55%, var(--card) 40%, var(--card-shade) 100%);
    box-shadow: 0 10px 30px rgba(0,0,0,.15);
  }
  .card-band { position: absolute; inset: 0; width: 100%; height: 100%; }
  .holder { position: absolute; left: 36px; top: 30px; color: #fff; }
  .holder-name { font-size: 22px; font-weight: 500; letter-spacing: 1px; text-transform: uppercase; }
  .holder-role { font-size: 13px; font-weight: 400; letter-spacing: 1px; text-transform: uppercase; margin-top: 3px; }
  .contact {
    position: absolute; left: 36px; top: 132px; list-style: none;
    font-size: 10.5px; color: var(--ink);
  }
  .contact-services { margin-bottom: 8px; line-height: 1.45; }
  .contact-line { display: flex; align-items: center; gap: 9px; height: 17px; white-space: nowrap; }
  .contact-line svg { width: 11px; height: 11px; flex: none; fill: var(--wine); }
  .brand { position: absolute; display: flex; align-items: center; gap: 12px; }
  .brand-dot { border-radius: 50%; background: var(--accent); flex: none; }
  .brand-name { color: var(--wine); font-weight: 500; white-space: nowrap; }
  .card-front .brand { right: 34px; bottom: 46px; }
  .card-front .brand-dot { width: 40px; height: 40px; }
  .card-front .brand-name { font-size: 22px; }
  .card-back .brand { left: 50%; top: 50%; transform: translate(-50%,-50%); }
  .card-back .brand-dot { width: 52px; height: 52px; }
  .card-back .brand-name { font-size: 32px; }
</style>
</head>
<body>
<main class="canvas">
  <section class="card card-front">
    <svg class="card-band" viewBox="0 0 520 300" preserveAspectRatio="none" aria-hidden="true">
      <path d="M0 0 H520 V70 C420 66 320 84 220 100 C140 112 60 116 0 114 Z" fill="var(--wine)"/>
      <path d="M60 118 C160 112 260 98 340 86 C410 76 470 72 520 74" stroke="var(--gold)" stroke-width="3" fill="none"/>
      <path d="M140 124 C230 114 310 100 380 91 C440 84 485 82 520 83" stroke="var(--gold-light)" stroke-width="1.5" fill="none"/>
    </svg>
    <div class="holder">
      <h1 class="holder-name">Marla Pennick</h1>
      <p class="holder-role">Prenatal Yoga Teacher</p>
    </div>
    <ul class="contact">
      <li class="contact-services">• Pre and Post Natal Yoga<br>• Pregnancy Workshops<br>• Hypnobirthing Courses</li>
      <li class="contact-line"><svg viewBox="0 0 12 12"><path d="M2 1h2.5l1 3-1.5 1a7 7 0 0 0 3 3l1-1.5 3 1V10a1 1 0 0 1-1 1A9 9 0 0 1 1 2a1 1 0 0 1 1-1z"/></svg>0491 352 718</li>
      <li class="contact-line"><svg viewBox="0 0 12 12"><rect x="3" y="0.5" width="6" height="11" rx="1"/></svg>Mobile 0491 352 718</li>
      <li class="contact-line"><svg viewBox="0 0 12 12"><rect x="1" y="1" width="10" height="10" rx="1.5"/></svg>stretchbelliesbayridgefield</li>
      <li class="contact-line"><svg viewBox="0 0 12 12"><rect x="0.5" y="2.5" width="11" height="7" rx="1"/></svg>hello@stretchbellies.com</li>
      <li class="contact-line"><svg viewBox="0 0 12 12"><circle cx="6" cy="6" r="5.5"/></svg>www.stretchbellies.com</li>
    </ul>
    <div class="brand">
      <span class="brand-dot"></span>
      <span class="brand-name">Stretch Bellies</span>
    </div>
  </section>

  <section class="card card-back">
    <div class="brand">
      <span class="brand-dot"></span>
      <span class="brand-name">Stretch Bellies</span>
    </div>
  </section>
</main>
</body>
</html>
```